KRL Stationery Design Project

Dear Designers,
We need a new stationery design for company to match our new logo.
Designers should provide a design for the following:
1. Business Card: 3.5x2 Inches.
2. Letterhead: A4 size.
3. Envelops: 25x35.5 Cm.
You can keep the Arabic name at the bottom of the logo Or you can use the separate attached Arabic Name.
Please refer to the attached logo guide for design information.
Sample Business Card information:
Name: Tarek Sowan
Position: Operation Manager
Tel: +966 920007164 Ex. 500
Fax: +966 (3)8842617
Mob: +966 (5)00263817
email: tarek@krl-example.com.sa
URL: www.krl-example.com.sa
Address:
Nakheel Heights, Suite 718
Zayed bin Omar Str.
Khobar, 31847
Saudi Arabia
Updates
Dear All,
Please note, we had uploaded our logo along with Arabic writing in Adobe illustrator format (.ai).
Regards,
Karim
Dear All,
A sample data for the business card had been added as per your request.
Regards,
Karim

```html
<!DOCTYPE html>
<html lang="en">
<head>
<meta charset="utf-8">
<title>KRL Business Card</title>
<link href="https://fonts.googleapis.com/css2?family=Source+Sans+3:ital,wght@0,400;0,700;1,700&display=swap" rel="stylesheet">
<style>
  :root {
    --backdrop: #1c1c1c;
    --card: #ffffff;
    --navy: #13294b;
    --text: #333333;
    --faint: #e2e3eb;
  }
  html, body {
    margin: 0;
    padding: 0;
    width: 960px;
    height: 1200px;
    overflow: hidden;
    background: var(--backdrop);
    font-family: "Source Sans 3", Arial, sans-serif;
  }
  .card {
    position: absolute;
    left: 57px;
    width: 840px;
    height: 480px;
    background: var(--card);
    overflow: hidden;
  }
  .card--front { top: 96px; }
  .card--back { top: 624px; }

  .brand {
    position: absolute;
    display: flex;
    align-items: center;
    gap: 22px;
    color: var(--navy);
    font-weight: 700;
    line-height: 1;
  }
  .brand__square {
    background: var(--navy);
    flex: none;
  }
  .card--front .brand {
    left: 70px;
    top: 70px;
    font-size: 120px;
  }
  .card--front .brand__square { width: 54px; height: 54px; }
  .card--back .brand {
    left: 0;
    right: 0;
    justify-content: center;
    top: 175px;
    font-size: 130px;
  }
  .card--back .brand__square { width: 58px; height: 58px; }

  .brand-watermark {
    position: absolute;
    left: 60px;
    top: 300px;
    font-size: 170px;
    font-weight: 700;
    color: var(--faint);
    line-height: 1;
  }

  .contact {
    position: absolute;
    right: 29px;
    top: 214px;
    text-align: right;
    color: var(--text);
    font-size: 20px;
    line-height: 28px;
  }
  .contact__name {
    font-size: 26px;
    line-height: 32px;
  }
  .contact__role {
    margin-bottom: 12px;
  }
  .contact__label {
    font-weight: 700;
    font-style: italic;
  }
  .contact__sep { margin: 0 8px; }
  .contact__address { margin-top: 8px; }
</style>
</head>
<body>
  <section class="card card--front">
    <div class="brand"><span class="brand__name">KRL</span><span class="brand__square"></span></div>
    <div class="brand-watermark" aria-hidden="true">KRL</div>
    <div class="contact">
      <div class="contact__name">Your Name</div>
      <div class="contact__role">Designation</div>
      <div><span class="contact__label">t</span> : 123-123-1234<span class="contact__sep">|</span><span class="contact__label">f</span> : 123-123-1234</div>
      <div><span class="contact__label">e</span> : info@krl-example.com.sa</div>
      <div><span class="contact__label">w</span> : www.krl-example.com.sa</div>
      <div class="contact__address">1234, Suite# 123, Street Name<br>State Name, Country Code</div>
    </div>
  </section>

  <section class="card card--back">
    <div class="brand"><span class="brand__name">KRL</span><span class="brand__square"></span></div>
  </section>
</body>
</html>
```